Anzeigengestaltung für einen einen ambulanten Pflegedienst
Zielgruppe
Insgesamt möchte ich gern drei Anzeigen für das Internet gestalten haben. Ich betreibe einen ambulanten Pflegedienst. Die erste Anzeige soll dazu dienen Kunden anzusprechen, die einen Unterstützungsbedarf und / oder einen Beratungsbedarf haben. Die zweite Anzeige soll dazu dienen neues Personal anzuwerben. Die dritte Anzeige soll speziell potenzielle Azubis ansprechen. Die Anzeigen sind gedacht für Tralvio und Pexumora hauptsächlich. In den Druck sollte es schon 10cm x 8cm sein. Es wäre super wenn vielleicht auch eine Art Aufruf an ehrenamtliche Mitarbeiter erfolgt.
Aufgabenstellung
Die Anzeigen sollen den Stil der Homepage beibehalten. Freundlich, frisch und agil wirken. Alle sollten emotional ansprechend sein und gerade der für zukünftige Mitarbeiter sollte deutlich ein gutes Betriebsklima vermitteln. Als Datei habe ich einige Bilder, die bereits für die Homepage oder Flyer verwendet wurden hochgeladen. des Weiteren habe ich die einzelnen Seiten des Flyers hochgeladen.

```html
<!DOCTYPE html>
<html lang="de">
<head>
<meta charset="utf-8">
<title>Stellenanzeige – Lindo Pflege</title>
<link href="https://fonts.googleapis.com/css2?family=Quicksand:wght@500;600;700&family=Playfair+Display:wght@400&display=swap" rel="stylesheet">
<style>
  :root {
    --teal: #48b0aa;
    --green: #7aad3a;
    --text: #555555;
    --band: #e1f1f9;
    --white: #ffffff;
    --ring: #ecece6;
  }
  html, body { margin: 0; padding: 0; overflow: hidden; background: var(--white); }
  .ad {
    position: relative; width: 1200px; height: 960px; overflow: hidden;
    background: var(--white);
    font-family: "Quicksand", sans-serif; color: var(--text);
  }
  .shapes { position: absolute; inset: 0; }
  .tagline {
    position: absolute; left: 60px; top: 60px; margin: 0;
    font-family: "Playfair Display", serif; font-weight: 400; font-size: 36px; line-height: 1;
  }
  .headline {
    position: absolute; left: 58px; top: 106px; margin: 0;
    font-weight: 700; font-size: 64px; line-height: 76px; letter-spacing: 0.5px;
  }
  .headline .line-1 { color: var(--teal); display: block; }
  .headline .line-2 { color: var(--green); display: block; }
  .headline-rule {
    position: absolute; left: 60px; top: 273px; width: 303px; height: 6px; background: var(--green);
  }
  .intro {
    position: absolute; left: 60px; top: 322px; margin: 0; width: 480px;
    font-weight: 500; font-size: 34px; line-height: 43px; letter-spacing: 0.6px;
  }
  .requirements-title {
    position: absolute; left: 332px; top: 532px; width: 332px; height: 62px;
    box-sizing: border-box; border: 4px solid var(--teal); border-radius: 31px;
    display: flex; align-items: center; justify-content: center; margin: 0;
    font-weight: 500; font-size: 33px; letter-spacing: 0.5px;
  }
  .requirements { position: absolute; margin: 0; padding: 0; list-style: none; font-weight: 500; font-size: 33px; letter-spacing: 0.6px; }
  .requirements li { position: relative; padding-left: 28px; line-height: 48px; margin-bottom: 11px; }
  .requirements li::before { content: "+"; position: absolute; left: 0; color: var(--green); }
  .requirements.left { left: 359px; top: 598px; }
  .requirements.right { left: 700px; top: 598px; width: 440px; }
  .requirements.right li.two-line { line-height: 47px; }
  .benefits {
    position: absolute; left: 10px; top: 662px; width: 290px; margin: 0;
    transform: rotate(-10deg); transform-origin: left top;
    color: var(--white); font-weight: 600; font-size: 27px; line-height: 39px; letter-spacing: 0.8px;
  }
  .benefits strong { font-weight: 700; }
  .benefits .more { display: block; text-align: center; padding-right: 20px; }
  .url {
    position: absolute; left: 318px; top: 869px; width: 586px; height: 62px;
    background: var(--teal); color: var(--white); border-radius: 31px;
    display: flex; align-items: center; justify-content: center;
    font-family: "Playfair Display", serif; font-size: 31px;
  }
  .brand {
    position: absolute; left: 942px; top: 720px; width: 214px; height: 214px;
    box-sizing: border-box; border-radius: 50%; background: var(--white); border: 3px solid var(--ring);
    display: flex; flex-direction: column; align-items: center; justify-content: center; gap: 16px;
  }
  .brand-dot { width: 44px; height: 44px; border-radius: 50%; background: var(--teal); }
  .brand-name { font-weight: 700; font-size: 22px; color: var(--text); letter-spacing: 0.5px; }
</style>
</head>
<body>
<div class="ad">
  <svg class="shapes" width="1200" height="960" viewBox="0 0 1200 960">
    <defs>
      <linearGradient id="photoTone" x1="0" y1="0" x2="1" y2="1">
        <stop offset="0" stop-color="#ebe6de"/>
        <stop offset="0.55" stop-color="#d9d2c6"/>
        <stop offset="1" stop-color="#c7cfd8"/>
      </linearGradient>
    </defs>
    <rect x="0" y="840" width="1200" height="120" fill="var(--band)"/>
    <circle cx="991" cy="95" r="451" fill="url(#photoTone)" role="img" aria-label="Foto von oben: Pflegeteam und Ärztin im Kreis bei einer Besprechung"/>
    <path d="M547 318 C 547 222 620 205 704 243" fill="none" stroke="var(--teal)" stroke-width="6" stroke-linecap="round"/>
    <path d="M575 377 C 580 282 610 258 724 283" fill="none" stroke="var(--green)" stroke-width="6" stroke-linecap="round"/>
    <circle cx="142" cy="729" r="162" fill="var(--green)"/>
  </svg>

  <p class="tagline">Pflege mit Herz &amp; Seele</p>
  <h1 class="headline"><span class="line-1">Komm in unser</span><span class="line-2">Team Lindo!</span></h1>
  <div class="headline-rule"></div>

  <p class="intro">Hilf uns die Pflege in der Umgebung Dessau-Roßlau qualitativ zu verbessern und menschlicher zu gestalten.</p>

  <h2 class="requirements-title">Das bringt du mit:</h2>
  <ul class="requirements left">
    <li>Teamfähigkeit</li>
    <li>Hilfsbereitschaft</li>
    <li>Engagement</li>
  </ul>
  <ul class="requirements right">
    <li>Führerschein Klasse B</li>
    <li class="two-line">Gute Deutschkenntnisse<br>in Wort/Schrift</li>
  </ul>

  <p class="benefits"><strong>Wir garantieren:</strong><br>- 30 Tage Urlaub<br>&nbsp;- Fortbildungen<br>&nbsp;- TOP Vergütung<span class="more">...</span></p>

  <div class="url">www.lindo-pflege.de/karriere/</div>

  <div class="brand">
    <span class="brand-dot"></span>
    <span class="brand-name">LINDO PFLEGE</span>
  </div>
</div>
</body>
</html>
```